Business card design for my company.
I would like the card's background colour to be black. You can also see our web site to get an idea of our brand. https://www.tmwhomecrafting.com.au/
- Name
- Email

```html
<!DOCTYPE html>
<html lang="en">
<head>
<meta charset="utf-8">
<title>TMW Home Crafting – Business Card</title>
<link href="https://fonts.googleapis.com/css2?family=Montserrat:wght@400;500;700;800&display=swap" rel="stylesheet">
<style>
  :root {
    --page-bg: #c9c9c9;
    --card-bg: #222222;
    --brand-green: #16973f;
    --text-white: #f4f4f4;
    --text-muted: #d8d8d8;
    --sheen-light: #5a5a5a;
    --sheen-dark: #262626;
  }
  * { margin: 0; padding: 0; box-sizing: border-box; }
  html, body {
    width: 1200px; height: 802px; overflow: hidden;
    background: linear-gradient(180deg, #d4d4d4 0%, #b3b3b3 100%);
    font-family: "Montserrat", sans-serif;
  }
  .stage {
    width: 1200px; height: 802px;
    display: flex; align-items: center; justify-content: center; gap: 40px;
  }
  .card {
    position: relative;
    width: 540px; height: 306px;
    background: var(--card-bg);
    border-radius: 16px;
    overflow: hidden;
    box-shadow: 0 14px 30px rgba(0,0,0,0.28);
  }
  .card-front .green-band {
    position: absolute; left: 0; right: 0; bottom: 0; height: 7px;
    background: var(--brand-green);
  }
  .card-front .sheen {
    position: absolute; inset: 0;
    width: 540px; height: 306px;
  }
  .brand-name {
    display: flex; align-items: center; gap: 10px;
    color: var(--text-white);
    font-weight: 800;
  }
  .brand-mark {
    width: 14px; height: 14px; background: var(--brand-green); flex: none;
  }
  .brand-lines { display: flex; flex-direction: column; line-height: 1; }
  .card-front .brand-name {
    position: absolute; left: 30px; top: 34px;
  }
  .card-front .brand-lines .big { font-size: 40px; letter-spacing: 1px; }
  .card-front .brand-lines .small { font-size: 10px; letter-spacing: 2.4px; margin-top: 6px; }
  .person {
    position: absolute; left: 30px; top: 148px;
  }
  .person-name {
    color: var(--brand-green);
    font-weight: 700; font-size: 19px; letter-spacing: 0.6px;
  }
  .person-title {
    color: var(--text-white); font-size: 12px; font-weight: 400; margin-top: 3px;
  }
  .divider {
    width: 10px; height: 2px; background: var(--brand-green); margin: 12px 0 10px;
  }
  .contact-list { list-style: none; }
  .contact-list li {
    display: flex; align-items: center; gap: 7px;
    color: var(--text-muted); font-size: 11.5px; font-weight: 500;
    margin-bottom: 8px;
  }
  .contact-list svg { width: 10px; height: 10px; flex: none; }
  .card-back .brand-name {
    position: absolute; left: 50%; top: 50%; transform: translate(-50%, -50%);
    gap: 14px;
  }
  .card-back .brand-mark { width: 20px; height: 20px; }
  .card-back .brand-lines .big { font-size: 66px; letter-spacing: 2px; }
  .card-back .brand-lines .small { font-size: 14px; letter-spacing: 4.6px; margin-top: 8px; }
</style>
</head>
<body>
<main class="stage">
  <section class="card card-front">
    <svg class="sheen" viewBox="0 0 540 306" aria-hidden="true">
      <defs>
        <linearGradient id="sheenGrad" x1="0" y1="1" x2="1" y2="0">
          <stop offset="0" stop-color="var(--sheen-dark)"/>
          <stop offset="0.7" stop-color="var(--sheen-light)"/>
          <stop offset="1" stop-color="#3a3a3a"/>
        </linearGradient>
      </defs>
      <path d="M150 306 L445 118 L540 182 L540 208 L445 146 L195 306 Z" fill="url(#sheenGrad)"/>
    </svg>

    <div class="brand-name">
      <span class="brand-mark"></span>
      <span class="brand-lines"><span class="big">TMW</span><span class="small">HOME CRAFTING</span></span>
    </div>

    <div class="person">
      <p class="person-name">DANIEL HARLOW</p>
      <p class="person-title">CEO/Founder</p>
      <div class="divider"></div>
      <ul class="contact-list">
        <li>
          <svg viewBox="0 0 10 10"><path d="M2 0.5 L4 2.8 L3 4 Q4 6 6 7 L7.2 6 L9.5 8 L8.2 9.5 Q4 9.5 0.5 1.8 Z" fill="var(--brand-green)"/></svg>
          555-204-7719
        </li>
        <li>
          <svg viewBox="0 0 10 10"><rect x="0.5" y="2" width="9" height="6.5" fill="var(--brand-green)"/><path d="M0.5 2 L5 5.6 L9.5 2" stroke="var(--card-bg)" stroke-width="0.9" fill="none"/></svg>
          info@tmwhomecrafting.com.au
        </li>
        <li>
          <svg viewBox="0 0 10 10"><circle cx="5" cy="5" r="4.5" fill="var(--brand-green)"/><path d="M0.5 5 H9.5 M5 0.5 V9.5" stroke="var(--card-bg)" stroke-width="0.7"/></svg>
          www.tmwhomecrafting.com.au
        </li>
      </ul>
    </div>
    <div class="green-band"></div>
  </section>

  <section class="card card-back">
    <div class="brand-name">
      <span class="brand-mark"></span>
      <span class="brand-lines"><span class="big">TMW</span><span class="small">HOME CRAFTING</span></span>
    </div>
  </section>
</main>
</body>
</html>
```